Pavecrest Works

Im looking for something similar to (tarvalepaving.com) web site. I really want it to pop!
services we offer:
- Seal Coating
- Crack Filling
- Striping
- Asphalt
- Concrete
- Signage
- Road Grinding
- Grading
- Hydro Blasting
- Recycled asphalt
- Dumpster Pads
- Pressure Washing
- Wheel blocks
- Bollard installation
- Commercial Curbing
- Job site clean up
- Sweeping
- Forestry Clean up
- ADA Compliant work
- Speed bump installation and removal
- Snow removal
- Custom stair sets (Commercial)
Target Market(s)
Parking lot maintenance, asphalt repairs, road grading
Industry/Entity Type
construction, parking lot maintenance
Number of Pages Required
2 page

```html
<!DOCTYPE html>
<html lang="en">
<head>
<meta charset="utf-8">
<title>Pavecrest Works</title>
<link rel="stylesheet" href="https://fonts.googleapis.com/css2?family=Montserrat:wght@400;500;600;700;800&display=swap">
<style>
:root{
  --green:#5cff00;
  --green-soft:#b6ff8a;
  --dark:#1f1f1f;
  --card:#333333;
  --asphalt:#3a3b3d;
  --asphalt-deep:#222324;
  --brick:#7a2e2f;
  --white:#ffffff;
  --text-grey:#555555;
}
*{margin:0;padding:0;box-sizing:border-box}
html,body{width:1200px;height:4173px;overflow:hidden;background:var(--white);font-family:'Montserrat',sans-serif}
.page{position:relative;width:1200px;height:4173px;overflow:hidden}
.abs{position:absolute}
.btn{position:absolute;background:var(--green);color:#111;font-weight:700;font-size:15px;display:flex;align-items:center;justify-content:center}

/* header */
.site-header{left:0;top:0;width:1200px;height:141px;background:var(--white);z-index:3}
.brand{left:112px;top:45px;width:240px;height:70px;color:#111;font-weight:800;line-height:1}
.brand .name{font-size:40px;letter-spacing:1px}
.brand .tag{font-size:15px;letter-spacing:9px;font-weight:700;margin-top:6px}
.top-band{left:0;top:0;width:1200px;height:62px}
.top-band .call{position:absolute;left:613px;top:22px;font-size:14px;color:#1a1a1a;letter-spacing:.3px}
.top-band .phone{position:absolute;left:948px;top:17px;font-size:20px;font-weight:700;color:#1a1a1a}
.main-nav{left:550px;top:90px;display:flex;gap:19px;font-size:16px;color:#444}
.header-btn{left:916px;top:81px;width:170px;height:42px}

/* hero */
.hero{left:0;top:141px;width:1200px;height:800px;background:linear-gradient(180deg,#4c4f52 0%,var(--asphalt) 30%,var(--asphalt-deep) 100%)}
.hero-kicker{left:0;top:378px;width:1200px;text-align:center;color:var(--white);font-size:40px;font-weight:700}
.hero-title{left:0;top:430px;width:1200px;text-align:center;color:var(--white);font-size:102px;font-weight:800;letter-spacing:2px}
.dots{width:16px}
.dots span{display:block;width:13px;height:13px;border-radius:50%;background:var(--white);margin-bottom:10px}
.dots span.on{background:var(--green)}

.seg-card{top:661px;width:471px;height:450px;z-index:2}
.seg-card .photo{width:471px;height:379px}
.seg-card .label{height:71px;background:var(--green);display:flex;align-items:center;justify-content:center;font-weight:700;font-size:21px;color:#111;letter-spacing:.5px}

/* who we are + services */
.brick{left:0;top:1100px;width:1200px;height:1240px;background:linear-gradient(180deg,#8a3a3a 0%,var(--brick) 40%,#5e2527 100%)}
.section-title{position:absolute;left:0;width:1200px;text-align:center;color:var(--white);font-weight:700}
.about-copy{left:240px;top:1262px;width:720px;text-align:center;color:#f1e4e4;font-size:13.5px;line-height:25px}
.svc-card{top:1807px;width:306px;height:290px;background:var(--card)}
.svc-card h3{position:absolute;left:0;top:118px;width:306px;text-align:center;color:var(--green);font-size:21px;font-weight:700}
.svc-card p{position:absolute;left:18px;top:158px;width:270px;text-align:center;color:#e6e6e6;font-size:13px;line-height:23px}
.svc-icon{top:1714px;width:172px;height:172px;border-radius:50%;background:var(--green-soft);border:4px solid var(--card);z-index:2}
.svc-icon .inner{position:absolute;left:10px;top:10px;width:144px;height:144px;border-radius:50%;background:var(--green-soft);border:3px solid #2f6b00}
.learn{top:2076px;width:152px;height:42px;font-size:14px}
.view-more{left:112px;top:2158px;width:974px;height:65px;font-size:25px;letter-spacing:.8px}

/* estimates */
.estimates{left:0;top:2335px;width:1200px;height:286px;background:linear-gradient(180deg,#4a4c4f 0%,var(--asphalt-deep) 100%)}
.estimates h2{position:absolute;left:0;top:46px;width:1200px;text-align:center;color:var(--green);font-size:40px;font-weight:800}
.estimates p{position:absolute;left:300px;top:100px;width:600px;text-align:center;color:var(--white);font-size:21px;font-weight:700;line-height:30px}
.estimates .btn{left:515px;top:187px;width:170px;height:43px;background:#151515;color:var(--green)}

/* gallery */
.gallery-title{left:0;top:2690px;width:1200px;text-align:center;font-size:38px;font-weight:800;color:#111}
.shot{position:absolute}

/* footer */
.footer-bg{left:0;top:3470px;width:1200px;height:703px}
.f-brand{left:0;top:3640px;width:1200px;text-align:center;color:var(--white);font-weight:800}
.f-brand .name{font-size:64px;letter-spacing:2px}
.f-brand .tag{font-size:24px;letter-spacing:14px;margin-top:4px}
.f-col{top:3856px;color:var(--white);font-size:15px}
.f-col h4{font-size:16px;font-weight:700;letter-spacing:.4px}
.f-col h4::after{content:"";display:block;width:36px;height:3px;background:var(--green);margin-top:12px}
.f-col ul{list-style:none;margin-top:20px}
.f-col li{line-height:29px}
.contact-row{display:flex;gap:14px;align-items:flex-start;line-height:24px;margin-bottom:22px}
.contact-row svg{flex:none;margin-top:4px}
.news-copy{font-size:13.5px;line-height:23px;margin-top:16px;width:245px}
.news-form{display:flex;margin-top:14px}
.news-form .field{width:196px;height:44px;background:var(--white);color:#999;font-size:12px;padding:14px 18px}
.news-form .send{width:50px;height:44px;background:var(--green);display:flex;align-items:center;justify-content:center}
.f-rule{left:112px;top:4091px;width:976px;height:1px;background:#555}
.copyright{left:0;top:4124px;width:1200px;text-align:center;color:#ddd;font-size:12.5px}
</style>
</head>
<body>
<div class="page">

  <!-- header -->
  <header class="site-header abs">
    <svg class="top-band abs" width="1200" height="62" viewBox="0 0 1200 62"><polygon points="582,0 1200,0 1200,62 555,62" fill="#5cff00"/></svg>
    <div class="top-band abs" style="background:none">
      <span class="call">CALL US TODAY FOR A FREE ESTIMATE</span>
      <span class="phone">555-014-2290</span>
    </div>
    <div class="brand abs"><div class="name">PAVECREST</div><div class="tag">WORKS</div></div>
    <nav class="main-nav abs"><span>Home</span><span>About</span><span>Services</span><span>Blog</span><span>Contact</span></nav>
    <div class="btn header-btn">Get Started Now!</div>
  </header>

  <!-- hero -->
  <section class="hero abs" role="img" aria-label="Wide asphalt road with lane markings and a city skyline in the distance"></section>
  <div class="hero-kicker abs">WELCOME TO</div>
  <div class="hero-title abs">PAVECREST</div>
  <div class="btn" style="left:515px;top:550px;width:170px;height:43px">Get Started Now!</div>
  <div class="dots abs" style="left:1149px;top:387px"><span></span><span class="on"></span><span></span></div>

  <svg class="abs" style="left:0;top:740px" width="1200" height="420" viewBox="0 0 1200 420">
    <polygon points="0,180 1200,0 1200,420 0,420" fill="#ffffff"/>
    <polygon points="0,180 1200,0 1200,22 0,200" fill="#5cff00"/>
  </svg>

  <div class="seg-card abs" style="left:112px">
    <div class="photo" role="img" aria-label="Night highway underpass with light trails and city towers" style="background:linear-gradient(160deg,#6f8ea8 0%,#2b3a4a 50%,#151a20 100%)"></div>
    <div class="label">COMMERCIAL</div>
  </div>
  <div class="seg-card abs" style="left:616px">
    <div class="photo" role="img" aria-label="Residential street lined with houses and trees under a blue sky" style="background:linear-gradient(180deg,#6fb6e6 0%,#a9cde6 35%,#7d8b4a 60%,#555a5e 100%)"></div>
    <div class="label">RESIDENTIAL</div>
  </div>

  <!-- who we are + services -->
  <section class="brick abs" role="img" aria-label="Red brick paving laid in a herringbone pattern"></section>
  <svg class="abs" style="left:0;top:1090px" width="1200" height="90" viewBox="0 0 1200 90"><polygon points="0,0 1200,0 1200,10 0,80" fill="#ffffff"/></svg>

  <h2 class="section-title" style="top:1210px;font-size:39px">WHO WE ARE</h2>
  <p class="about-copy abs">Lorem Ipsum is simply dummy text of the printing and typesetting industry. Lorem Ipsum has been the industry's standard dummy text ever since the 1500s, when an unknown printer took a galley of type and scrambled it to make a type specimen book. It has survived not only five centuries, but also the leap into electronic typesetting, remaining essentially unchanged. It was popularised in the 1960s with the release of Lettrex sheets containing Lorem Ipsum passages, and more recently with desktop publishing software like Pagesetter Pro including versions of Lorem Ipsum.</p>
  <div class="btn" style="left:515px;top:1440px;width:170px;height:42px">Get Started Now!</div>

  <h2 class="section-title" style="top:1610px;font-size:39px">SERVICES</h2>
  <div class="dots abs" style="left:1149px;top:1935px"><span></span><span class="on"></span><span></span></div>

  <div class="svc-icon abs" style="left:179px"><div class="inner" role="img" aria-label="Spray gun pictogram"></div></div>
  <div class="svc-icon abs" style="left:514px"><div class="inner" role="img" aria-label="Crack filling machine pictogram"></div></div>
  <div class="svc-icon abs" style="left:849px"><div class="inner" role="img" aria-label="Worker striping pavement pictogram"></div></div>

  <article class="svc-card abs" style="left:112px"><h3>Seal Coating</h3><p>Lorem ipsum dolor sit amet, consectetur adipiscing elit, sed do eiusmod tempor incididunt ut labore et dolore magna aliqua. Quis ipsum</p></article>
  <article class="svc-card abs" style="left:447px"><h3>Crack Filling</h3><p>Lorem ipsum dolor sit amet, consectetur adipiscing elit, sed do eiusmod tempor incididunt ut labore et dolore magna aliqua. Quis ipsum</p></article>
  <article class="svc-card abs" style="left:782px"><h3>Striping</h3><p>Lorem ipsum dolor sit amet, consectetur adipiscing elit, sed do eiusmod tempor incididunt ut labore et dolore magna aliqua. Quis ipsum</p></article>
  <div class="btn learn" style="left:189px">Learn More &gt;</div>
  <div class="btn learn" style="left:524px">Learn More &gt;</div>
  <div class="btn learn" style="left:859px">Learn More &gt;</div>
  <div class="btn view-more">VIEW MORE OUR SERVICES</div>

  <!-- free estimates -->
  <section class="estimates abs" role="img" aria-label="Two-lane asphalt road with yellow centre lines">
    <h2>FREE ESTIMATES</h2>
    <p>Neque porro quisquam est qui dolorem ipsum quia dolor sit amet, consectetur, adipisci velit...</p>
    <div class="btn">Get Started Now!</div>
  </section>

  <!-- gallery -->
  <h2 class="gallery-title abs">OUR GALLERY</h2>
  <div class="shot" role="img" aria-label="Compact track loader with grading attachment on a gravel path" style="left:112px;top:2762px;width:391px;height:308px;background:linear-gradient(180deg,#4f6b3c 0%,#8a8a7a 55%,#6c6a63 100%)"></div>
  <div class="shot" role="img" aria-label="Freshly paved path through tall pine trees" style="left:528px;top:2762px;width:267px;height:308px;background:linear-gradient(180deg,#c9d3cf 0%,#3f5a35 40%,#4e4f4c 100%)"></div>
  <div class="shot" role="img" aria-label="Tracked loader grading a dirt road" style="left:819px;top:2762px;width:269px;height:308px;background:linear-gradient(180deg,#a9c7e0 0%,#5d6e45 35%,#8d7a5c 70%,#caa33a 100%)"></div>
  <div class="shot" role="img" aria-label="Worker sealing the floor of a parking garage" style="left:112px;top:3096px;width:267px;height:307px;background:linear-gradient(180deg,#8c8e8c 0%,#444a48 50%,#1e2120 100%)"></div>
  <div class="shot" role="img" aria-label="Yellow bollards installed beside utility meters" style="left:403px;top:3096px;width:267px;height:307px;background:linear-gradient(180deg,#9a9b94 0%,#c9b33a 50%,#707069 100%)"></div>
  <div class="shot" role="img" aria-label="Track loader grading soil beside a corn field" style="left:696px;top:3096px;width:392px;height:307px;background:linear-gradient(180deg,#c7d2da 0%,#a48a52 40%,#7a6446 75%,#5a4a38 100%)"></div>

  <!-- footer -->
  <svg class="footer-bg abs" width="1200" height="703" viewBox="0 0 1200 703" role="img" aria-label="Dark asphalt texture">
    <polygon points="0,183 1200,0 1200,703 0,703" fill="#161616"/>
  </svg>
  <div class="f-brand abs"><div class="name">PAVECREST</div><div class="tag">WORKS</div></div>

  <div class="f-col abs" style="left:112px">
    <h4>CONTACT US</h4>
    <div style="margin-top:20px">
      <div class="contact-row"><svg width="14" height="18" viewBox="0 0 14 18"><path d="M7 0a7 7 0 0 0-7 7c0 5 7 11 7 11s7-6 7-11a7 7 0 0 0-7-7zm0 10a3 3 0 1 1 0-6 3 3 0 0 1 0 6z" fill="#fff"/></svg><span>4820 Larkspur Avenue,<br>Millbrook, Colorado, 80000.</span></div>
      <div class="contact-row"><svg width="16" height="16" viewBox="0 0 16 16"><path d="M3.5 0l3 4-2 2c1 2 3 4 5 5l2-2 4 3-2 3.5C7 15 1 9 0 3.5z" fill="#fff"/></svg><span>555-014-2290</span></div>
      <div class="contact-row"><svg width="16" height="14" viewBox="0 0 16 14"><rect x="1" y="1" width="14" height="12" rx="1" fill="none" stroke="#fff" stroke-width="2"/><path d="M1 2l7 5 7-5" fill="none" stroke="#fff" stroke-width="2"/></svg><span>info@pavecrestworks.com</span></div>
    </div>
  </div>
  <div class="f-col abs" style="left:448px">
    <h4>SITEMAP</h4>
    <ul><li>Home</li><li>About</li><li>Services</li><li>Blog</li><li>Contact</li></ul>
  </div>
  <div class="f-col abs" style="left:662px">
    <h4>NEWSLETTER</h4>
    <p class="news-copy">Neque porro quisquam est qui dolorem ipsum quiavelit...</p>
    <div class="news-form"><div class="field">Email Address</div><div class="send"><svg width="22" height="20" viewBox="0 0 22 20"><path d="M0 9L22 0 17 20 10 14 18 4 7 12z" fill="#111"/></svg></div></div>
  </div>
  <div class="f-col abs" style="left:1012px">
    <h4>SOCIAL</h4>
    <ul><li>Chatterbook</li><li>Chirper</li><li>Linkwork</li><li>Viewtube</li></ul>
  </div>
  <div class="f-rule abs"></div>
  <div class="copyright abs">Pavecrest © 2021. All Rights Reserved.</div>
</div>
</body>
</html>
```